Veltrane Group Business Card Design

The CEO is looking for a new trendy look for his business card.
You can stay with current branding or come up with something new/creative. It can be 3D, including Medical Office buildings. You can use our logo in a variety of colors. Please include name, title, company name, company website, email address, cell number

Target Market(s)

Real Estate Development and Construction

Industry/Entity Type

Health care real estate

Contact Information for Business Card

Rohesh Kamdar, CEO M-604.781.2249 E-roheshkamdar@veltrane.com Address:4180 Lindqvist Ave, Tampa, FL 33482 www.veltrane.com

Font styles to use
Other font styles liked:
• Be creative

Requirements
Must have
• Creative, trendy look
Nice to have
• Please go to our website to get a feel- www. veltrane.com
Should not have
• small fonts

```html
<!DOCTYPE html>
<html lang="en">
<head>
<meta charset="utf-8">
<title>Veltrane Group Business Card</title>
<link href="https://fonts.googleapis.com/css2?family=Arimo:wght@400;700&display=swap" rel="stylesheet">
<style>
  :root {
    --backdrop: #b21e29;
    --card-dark: #262626;
    --card-light: #ececec;
    --brand-red: #b21e29;
    --brand-navy: #1c2b4a;
    --ink: #1a1a1a;
    --white: #ffffff;
  }
  * { margin: 0; padding: 0; box-sizing: border-box; }
  html, body {
    width: 1200px; height: 1000px; overflow: hidden;
    background: var(--backdrop);
    font-family: "Arimo", Arial, sans-serif;
  }
  .card {
    position: absolute; left: 214px; width: 772px; height: 440px;
  }
  .card-front { top: 36px; background: var(--card-dark); }
  .card-back { top: 507px; background: var(--card-light); }

  .brand-wordmark {
    position: absolute; font-weight: 700; white-space: nowrap;
    transform: translateX(-50%); letter-spacing: -1px;
  }
  .card-front .brand-wordmark {
    left: 386px; top: 168px; font-size: 74px; color: var(--white);
  }
  .card-back .brand-wordmark {
    left: 212px; top: 196px; font-size: 36px; color: var(--brand-red);
  }

  .divider {
    position: absolute; left: 364px; top: 51px; height: 340px;
    border-left: 2px dashed var(--ink);
  }
  .details { position: absolute; left: 424px; top: 80px; }
  .person-name {
    font-size: 33px; font-weight: 700; color: var(--brand-red);
    letter-spacing: 0.5px; line-height: 1;
  }
  .person-title {
    font-size: 18px; color: var(--brand-navy); margin-top: 8px; margin-left: 2px;
  }
  .contact-list { list-style: none; margin-top: 18px; }
  .contact-list li {
    display: flex; align-items: center; height: 31px;
    font-size: 20px; color: var(--ink);
  }
  .contact-list svg { width: 20px; height: 20px; margin-right: 10px; flex: none; }
  .company-name { font-size: 27px; margin-top: 14px; }
  .company-name .first { color: var(--brand-red); }
  .company-name .second { color: var(--brand-navy); }
  .address { font-size: 19px; color: var(--ink); line-height: 28px; margin-top: 6px; }
</style>
</head>
<body>
  <section class="card card-front">
    <div class="brand-wordmark">Veltrane Group</div>
  </section>

  <section class="card card-back">
    <div class="brand-wordmark">Veltrane Group</div>
    <div class="divider"></div>
    <div class="details">
      <div class="person-name">ROHESH KAMDAR</div>
      <div class="person-title">CEO</div>
      <ul class="contact-list">
        <li>
          <svg viewBox="0 0 20 20" fill="none" stroke="#1c2b4a" stroke-width="1.6">
            <rect x="5" y="1" width="10" height="18" rx="2"/>
            <line x1="8.5" y1="16" x2="11.5" y2="16"/>
          </svg>M-604.781.2249
        </li>
        <li>
          <svg viewBox="0 0 20 20" fill="#1c2b4a">
            <path d="M19 2 L1 9 L7 11 L9 18 L12 13 L19 2 Z M7 11 L17 4 L9 12 Z"/>
          </svg>roheshkamdar@veltrane.com
        </li>
        <li>
          <svg viewBox="0 0 20 20" fill="none" stroke="#1c2b4a" stroke-width="1.4">
            <circle cx="10" cy="10" r="8"/>
            <ellipse cx="10" cy="10" rx="3.5" ry="8"/>
            <line x1="2" y1="10" x2="18" y2="10"/>
          </svg>www.veltrane.com
        </li>
      </ul>
      <div class="company-name"><span class="first">Veltrane</span> <span class="second">Group</span></div>
      <div class="address">4180 Lindqvist Ave, Tampa,<br>FL 33482</div>
    </div>
  </section>
</body>
</html>
```